Harborlight Plans (03)

We're designing a website to sell Medicare Supplements. Attached is the script we want to say and general layout, but please use your best knowledge to make it better. This platform should be extremely user-friendly, but we want to make it look fun and approachable! Most Insurance/medicare websites are very boring, drab, simple but we want this one to be more personalized, fun and sexy (but again, still user-friendly since our target demographic is 65+).

This homepage should include a fun and inviting quiz, the script is in the attachment below. It should also include the blurbs about what medicare supplements plans are and why they should buy them. Feel free to play around with cool fonts and imagery, we want the site to be engaging!

Target Market(s)

seniors

Industry/Entity Type

Insurance

Number of Pages Required

1 page

Requirements
Must have
• Quiz, company name and tag line, script
Nice to have
• fun, engaging elements

```html
<!DOCTYPE html>
<html lang="en">
<head>
<meta charset="utf-8">
<title>Harborlight Plans</title>
<link href="https://fonts.googleapis.com/css2?family=Montserrat:wght@500;600;700&family=Roboto:wght@400;500;700&display=swap" rel="stylesheet">
<style>
:root{
  --teal:#1fa392;
  --teal-dark:#15806f;
  --ink:#222;
  --text:#333;
  --muted:#555;
  --page:#f4f4f4;
  --mint:#cde8e4;
  --hero-a:#1c3634;
  --hero-b:#2a4a47;
  --footer:#eef2f8;
  --line:#d4d8de;
}
*{margin:0;padding:0;box-sizing:border-box}
html,body{width:1200px;height:2611px;overflow:hidden}
body{position:relative;background:var(--page);font-family:'Roboto',sans-serif;color:var(--text)}
.abs{position:absolute}

/* header */
.site-header{left:0;top:0;width:1200px;height:70px;background:#fff}
.brand{display:flex;align-items:center;gap:10px;font-family:'Roboto',sans-serif;font-weight:700;font-size:21px;color:var(--ink)}
.brand-dot{width:26px;height:26px;border-radius:50%;background:var(--teal)}
.site-header .brand{left:173px;top:20px}
.nav a{position:absolute;top:26px;font-family:'Montserrat',sans-serif;font-size:17px;font-weight:500;color:var(--ink);text-decoration:none;white-space:nowrap}
.caret{font-size:9px;vertical-align:middle;color:var(--ink)}
.header-call{left:840px;top:26px;display:flex;align-items:center;gap:6px;font-family:'Montserrat',sans-serif;font-size:17px;font-weight:500;color:var(--ink)}
.header-call b{color:var(--teal);font-weight:600}

/* hero */
.hero{left:0;top:70px;width:1200px;height:380px}
.hero-title{left:0;top:150px;width:1200px;text-align:center;font-family:'Montserrat',sans-serif;font-weight:700;font-size:51px;color:#fff}
.hero-tag{left:0;top:224px;width:1200px;text-align:center;font-size:16px;font-weight:500;color:#fff}
.hero-call{left:0;top:262px;width:1200px;text-align:center;font-size:32px;font-weight:700;color:#fff}
.hero-call span{color:var(--teal)}

/* intro */
.intro-head{left:260px;top:485px;width:680px;text-align:center;font-size:30px;font-weight:500;line-height:41px;color:var(--text)}
.intro-rule{left:533px;top:675px;width:134px;height:4px;background:var(--teal);border-radius:2px}
.intro-copy{left:350px;top:700px;width:500px;text-align:center;font-size:18px;line-height:31px;color:var(--text)}

/* quiz */
.quiz-card{left:314px;top:808px;width:572px;height:690px;background:#fff;border-radius:26px;box-shadow:0 2px 10px rgba(0,0,0,.08)}
.quiz-title{left:446px;top:864px;font-size:25px;font-weight:700;color:var(--ink)}
.q-label{left:451px;font-size:21px;font-weight:500;color:var(--ink)}
.q-options{left:475px;list-style:none}
.q-options li{height:31px;font-size:15px;color:var(--text);display:flex;align-items:center;gap:8px}
.q-options li::before{content:"";width:8px;height:8px;border:2px solid var(--teal);border-radius:50%}
.zip{left:474px;top:1383px;width:284px;height:52px;border:1px solid #444;border-radius:26px;background:#fff;padding-left:24px;font-family:'Roboto',sans-serif;font-size:15px;color:#888;display:flex;align-items:center}

/* article */
.article{left:308px;width:612px;font-size:11px;line-height:23.2px;color:var(--ink)}
.article h2{font-size:14px;font-weight:700;margin-bottom:8px;margin-left:0}
.article p{padding-left:3px}
.article ul{list-style:none;padding-left:24px;margin-top:12px}
.article li{position:relative;padding-left:8px}
.article li::before{content:"";position:absolute;left:0;top:10px;width:4px;height:4px;border-radius:50%;background:var(--ink)}

/* footer */
.site-footer{left:0;top:2184px;width:1200px;height:427px;background:var(--footer);border-top:2px solid #e2e6ec}
.site-footer .brand{left:486px;top:2242px}
.f-rule{left:173px;width:855px;height:1px;background:var(--line)}
.f-col h3{font-family:'Montserrat',sans-serif;font-size:16px;font-weight:600;color:#333;margin-bottom:12px}
.f-col ul{list-style:none;font-size:11px;line-height:19.5px;color:#333}
.contact-row{display:flex;gap:14px;font-size:11px;line-height:19.5px;color:#333}
.contact-row svg{flex:none}
.copyright{left:173px;top:2566px;font-size:12px;color:#333}
.social{top:2562px;width:24px;height:24px;border-radius:50%;background:var(--teal)}
</style>
</head>
<body>

<header class="site-header abs">
  <div class="brand abs"><span class="brand-dot"></span>Harborlight Plans</div>
  <nav class="nav">
    <a style="left:467px">Medicare <span class="caret">▾</span></a>
    <a style="left:585px">Get Quotes</a>
    <a style="left:719px">Blog</a>
  </nav>
  <div class="header-call abs">
    <svg width="20" height="20" viewBox="0 0 24 24"><path d="M6.6 10.8a15 15 0 0 0 6.6 6.6l2.2-2.2c.3-.3.7-.4 1-.2 1.1.4 2.3.6 3.6.6.6 0 1 .4 1 1V20c0 .6-.4 1-1 1A17 17 0 0 1 3 4c0-.6.4-1 1-1h3.5c.6 0 1 .4 1 1 0 1.3.2 2.5.6 3.6.1.3 0 .7-.2 1z" fill="none" stroke="#1d3b38" stroke-width="1.6"/></svg>
    Call :<b>(800) 555-0142</b>
  </div>
</header>

<svg class="hero abs" width="1200" height="380" viewBox="0 0 1200 380" role="img" aria-label="Photo of a smiling senior couple relaxing at home, under a dark teal tint">
  <defs>
    <linearGradient id="heroTint" x1="0" y1="0" x2="1" y2="0">
      <stop offset="0" stop-color="#172e2c"/>
      <stop offset=".55" stop-color="#1f3a37"/>
      <stop offset="1" stop-color="#324f4b"/>
    </linearGradient>
  </defs>
  <rect width="1200" height="380" fill="var(--page)"/>
  <path d="M0 260 Q600 395 1200 282 L1200 0 L0 0 Z" fill="var(--mint)"/>
  <path d="M0 280 Q600 420 1200 305 L1200 380 L0 380 Z" fill="var(--page)"/>
  <path d="M0 275 Q520 390 1200 278 L1200 0 L0 0 Z" fill="url(#heroTint)"/>
</svg>
<h1 class="hero-title abs">Harborlight Plans</h1>
<p class="hero-tag abs">Be confident choosing the Medicare Supplement plan that's right for you.</p>
<p class="hero-call abs"><span>Call (800) 555-0142</span> to talk to a live agent.</p>

<h2 class="intro-head abs">We know insurance can be confusing. With so much information and not enough answers, we’re here to help you find the plan that works best for you, your family and your health.</h2>
<div class="intro-rule abs"></div>
<p class="intro-copy abs">Take this short quiz to to find flexible and affordable plans that you can feel confident in.</p>

<section class="quiz-card abs" aria-label="Quiz"></section>
<h3 class="quiz-title abs">Quiz Script:</h3>
<h4 class="q-label abs" style="top:912px">1. I am</h4>
<ul class="q-options abs" style="top:950px"><li>a. Over 64 years old</li><li>b. 64 years old</li><li>c. Under 64 years old</li></ul>
<h4 class="q-label abs" style="top:1069px">2. I am</h4>
<ul class="q-options abs" style="top:1108px"><li>a. Male</li><li>b. Female</li><li>c. Unspecified</li></ul>
<h4 class="q-label abs" style="top:1219px">3. I want to see</h4>
<ul class="q-options abs" style="top:1258px"><li>a. Free plans</li><li>b. Premium plans</li><li>c. All plans</li></ul>
<h4 class="q-label abs" style="top:1395px">4.</h4>
<div class="zip abs">Enter Zip Code</div>

<article class="article abs" style="top:1552px">
  <h2>What is a Medicare Supplement plan?</h2>
  <p>Each Medicare Supplement insurance plan offers a different level of basic benefits, but each lettered plan will include the same standardized basic benefits regardless of insurance company and location. Medicare Supplement insurance plans do not always cover vision, dental, long-term care, or hearing aids, but all plans must cover at least a portion of the following basic benefits:</p>
  <ul>
    <li>Medicare Part A coinsurance costs up to an additional 365 days after Medicare benefits are exhausted</li>
    <li>Medicare Part A hospice care coinsurance or copayments</li>
    <li>Medicare Part B coinsurance or copayments</li>
    <li>First three pints of blood used in a medical procedure</li>
  </ul>
</article>

<article class="article abs" style="top:1815px">
  <h2>Medicare Supplement insurance plan costs</h2>
  <p style="width:580px">Although private insurance companies are required to offer the same basic benefits for each lettered plan, they do have the ability to charge different premiums. You might want to shop around to find a Medicare Supplement insurance plan that may fit your medical and financial needs. Insurance companies may price their plan premiums in any of the following ways:</p>
  <ul>
    <li><b>Community no-age-rated:</b> These Medicare Supplement insurance plans charge premiums that are the same across the board, regardless of age.</li>
    <li><b>Issue-age-rated:</b> These plans base their premiums on your age when you first enrolled in the policy. Therefore, the younger you are when you enroll in this type of plan, the lower your premium will be.</li>
    <li><b>Attained-age-rated:</b> Like issue-age-rated, these plans base their premiums on the age you were when you first bought a policy, but unlike issue-age-rated, premiums increase as you get older.</li>
  </ul>
</article>

<footer class="site-footer abs"></footer>
<div class="brand abs" style="left:490px;top:2242px"><span class="brand-dot"></span>Harborlight Plans</div>
<div class="f-rule abs" style="top:2299px"></div>

<div class="f-col abs" style="left:173px;top:2326px">
  <h3>Contact</h3>
  <div class="contact-row"><svg width="22" height="26" viewBox="0 0 22 26"><path d="M11 24s8-8 8-14a8 8 0 0 0-16 0c0 6 8 14 8 14z" fill="none" stroke="var(--teal)" stroke-width="1.3"/><circle cx="11" cy="10" r="3" fill="none" stroke="var(--teal)" stroke-width="1.3"/></svg><span>412 Quayside Lane,<br>Port Elsmere, OR</span></div>
  <div class="contact-row" style="margin-top:14px"><svg width="22" height="24" viewBox="0 0 24 24"><path d="M6.6 10.8a15 15 0 0 0 6.6 6.6l2.2-2.2c.3-.3.7-.4 1-.2 1.1.4 2.3.6 3.6.6.6 0 1 .4 1 1V20c0 .6-.4 1-1 1A17 17 0 0 1 3 4c0-.6.4-1 1-1h3.5c.6 0 1 .4 1 1 0 1.3.2 2.5.6 3.6.1.3 0 .7-.2 1z" fill="none" stroke="var(--teal)" stroke-width="1.2"/></svg><span>8 800 555 014 21<br>8 800 555 019 76</span></div>
  <div class="contact-row" style="margin-top:14px"><svg width="22" height="24" viewBox="0 0 24 24"><rect x="1" y="6" width="22" height="14" fill="none" stroke="var(--teal)" stroke-width="1.2"/><path d="M1 6l11 8 11-8M1 20l8-7M23 20l-8-7" fill="none" stroke="var(--teal)" stroke-width="1.2"/></svg><span>hello@harborlightplans.com<br>team@harborlightplans.com</span></div>
</div>
<div class="f-col abs" style="left:440px;top:2326px"><h3>Company</h3><ul><li>Lorem ipsum dolo</li><li>Consectetur adipiscing elit.</li><li>Fusce eget leo tincid</li><li>Donec consequat</li><li>Praesent elementum</li><li>Jmauris posueret</li></ul></div>
<div class="f-col abs" style="left:657px;top:2326px"><h3>Information</h3><ul><li>Lorem ipsum dolo</li><li>Consectetur adipiscing elit.</li><li>Fusce eget leo tincid</li><li>Donec consequat</li><li>Praesent elementum</li><li>Jmauris posuer</li></ul></div>
<div class="f-col abs" style="left:886px;top:2326px"><h3>Other Links</h3><ul><li>Lorem ipsum dolo</li><li>Consectetur adipiscing elit.</li><li>Fusce eget leo tincid</li><li>Donec consequat</li><li>Praesent elementum</li><li>Jmauris posueret</li></ul></div>

<div class="f-rule abs" style="top:2538px"></div>
<p class="copyright abs">Copyright © 2020 Harborlight Plans. All Rights Reserved</p>
<span class="social abs" style="left:911px" aria-label="Social link"></span>
<span class="social abs" style="left:941px" aria-label="Social link"></span>
<span class="social abs" style="left:971px" aria-label="Social link"></span>
<span class="social abs" style="left:1002px" aria-label="Social link"></span>

</body>
</html>
```